Redesign of business card for Cedar Ridge Mechanical

We are looking for a new design for our business cards for Cedar Ridge Mechanical. We are a plumbing & HVAC construction company, operating on the West Coast of Canada and USA. Logo attached.
Industry/Entity Type
Construction - Plumbing & HVAC
Contact Information for Business Card
Name, address, phone numbers, email, website address
Look and feel
Each slider illustrates characteristics of the customer's brand and the style your logo design should communicate.

```html
<!DOCTYPE html>
<html lang="en">
<head>
<meta charset="utf-8">
<title>Cedar Ridge Mechanical – Business Card</title>
<link rel="stylesheet" href="https://fonts.googleapis.com/css2?family=Montserrat:wght@400;500;700&display=swap">
<style>
  :root {
    --backdrop: #6e6e6e;
    --card: #1b1b1b;
    --card-edge: #b9b9b9;
    --silver: #d6d6d6;
    --text: #bdbdbd;
    --muted: #9a9a9a;
    --rule: #8a8a8a;
  }
  * { box-sizing: border-box; margin: 0; padding: 0; }
  html, body { width: 1200px; height: 800px; overflow: hidden; }
  body {
    background: var(--backdrop);
    font-family: "Montserrat", sans-serif;
    display: flex;
    align-items: center;
    justify-content: center;
    gap: 40px;
  }
  .card {
    position: relative;
    width: 540px;
    height: 309px;
    background: var(--card);
    border: 2px solid var(--card-edge);
    border-radius: 20px;
    overflow: hidden;
    box-shadow: 0 14px 30px rgba(0,0,0,0.35);
  }
  /* Front */
  .brand-mark {
    position: absolute;
    left: 34px;
    top: 52px;
    display: flex;
    align-items: center;
    gap: 10px;
    color: var(--silver);
    font-weight: 700;
    font-size: 17px;
    letter-spacing: 1px;
    text-transform: uppercase;
    line-height: 1.25;
  }
  .brand-square {
    width: 18px; height: 18px;
    border: 2px solid var(--silver);
    flex: none;
  }
  .holder {
    position: absolute;
    right: 34px;
    top: 40px;
    text-align: right;
  }
  .holder-name {
    color: var(--silver);
    font-weight: 700;
    font-size: 21px;
    letter-spacing: 0.5px;
  }
  .holder-title {
    color: var(--muted);
    font-size: 13px;
    margin-top: 2px;
  }
  .rule-top {
    position: absolute;
    left: 270px; right: 34px; top: 112px;
    height: 1px; background: var(--rule);
  }
  .address {
    position: absolute;
    right: 34px;
    top: 126px;
    text-align: right;
    color: var(--text);
    font-size: 13px;
    line-height: 1.55;
  }
  .rule-bottom {
    position: absolute;
    left: 34px; width: 260px; top: 186px;
    height: 1px; background: var(--rule);
  }
  .contacts {
    position: absolute;
    left: 34px;
    top: 198px;
    list-style: none;
    color: var(--text);
    font-size: 13px;
    line-height: 1.6;
  }
  .contacts li { display: flex; align-items: center; gap: 10px; }
  .contacts svg { width: 11px; height: 11px; flex: none; }
  /* Back */
  .card-back .pattern {
    position: absolute; inset: 0;
    background: linear-gradient(120deg, #0f0f0f 0%, #1c1c1c 45%, #3a3a3a 100%);
  }
  .back-brand {
    position: absolute;
    right: 48px;
    top: 132px;
    display: flex;
    align-items: center;
    gap: 10px;
    color: var(--silver);
    font-weight: 700;
    font-size: 15px;
    letter-spacing: 1px;
    text-transform: uppercase;
  }
</style>
</head>
<body>
  <section class="card card-front">
    <div class="brand-mark"><span class="brand-square"></span><span>Cedar Ridge<br>Mechanical</span></div>

    <div class="holder">
      <p class="holder-name">MARCUS TRENT</p>
      <p class="holder-title">President</p>
    </div>
    <div class="rule-top"></div>
    <p class="address">4120 Harbor Lane<br>Suite 200, Tacoma, WA 98402</p>

    <div class="rule-bottom"></div>
    <ul class="contacts">
      <li><svg viewBox="0 0 12 12"><path d="M3 1 L5 3 L4 4.5 Q5.5 7 7.5 8 L9 7 L11 9 L9.5 11 Q3 10 1 2.5 Z" fill="#bdbdbd"/></svg>1-866-555-0142 Toll Free</li>
      <li><svg viewBox="0 0 12 12"><path d="M3 1 L5 3 L4 4.5 Q5.5 7 7.5 8 L9 7 L11 9 L9.5 11 Q3 10 1 2.5 Z" fill="#bdbdbd"/></svg>213-555-0187</li>
      <li><svg viewBox="0 0 12 12"><rect x="1" y="2.5" width="10" height="7" fill="#bdbdbd"/><path d="M1 2.5 L6 6.5 L11 2.5" stroke="#1b1b1b" fill="none"/></svg>info@cedarridgemech.com</li>
      <li><svg viewBox="0 0 12 12"><circle cx="6" cy="6" r="5" fill="none" stroke="#bdbdbd" stroke-width="1.2"/><ellipse cx="6" cy="6" rx="2" ry="5" fill="none" stroke="#bdbdbd"/><line x1="1" y1="6" x2="11" y2="6" stroke="#bdbdbd"/></svg>www.cedarridgemech.com</li>
    </ul>
  </section>

  <section class="card card-back">
    <div class="pattern" role="img" aria-label="Repeating glossy spot-varnish brand pattern across a black card back"></div>
    <div class="back-brand"><span class="brand-square"></span><span>Cedar Ridge Mechanical</span></div>
  </section>
</body>
</html>
```